Investor Presentation

We have a deck that is mostly finished that needs to be properly formatted and cleaned up. The presentation is for an investment in a financial firm. So the design we are looking for is very professional and minimalistic. A very clean look with conservative color schemes and fonts. The designer can leverage our existing logos, background, etc.

The final design files should have full editing functionality.

Target Market(s)

Sophisticated institutional investors

Industry/Entity Type

Conservative

Requirements
Nice to have
• Cleaned up / formatted tables from the attached files to add to the presentation.

```html
<!DOCTYPE html>
<html lang="en">
<head>
<meta charset="utf-8">
<title>Graph data Heading</title>
<link href="https://fonts.googleapis.com/css2?family=Ubuntu:wght@400;500&family=Roboto:wght@400&display=swap" rel="stylesheet">
<style>
  :root {
    --header-teal: #0b7479;
    --footer-teal: #3793a0;
    --heading-teal: #117a80;
    --text-dark: #3a3a3a;
    --bar-teal: #3793a0;
    --bar-cyan: #35cfe0;
    --bar-sky: #7bbdd6;
    --bar-deep: #0b9da8;
    --bar-grey: #777777;
    --axis: #4a4a4a;
    --white: #ffffff;
  }
  * { margin: 0; padding: 0; box-sizing: border-box; }
  html, body { width: 1200px; height: 900px; overflow: hidden; background: var(--white); }
  .slide {
    position: relative;
    width: 1200px;
    height: 900px;
    overflow: hidden;
    font-family: "Roboto", Arial, sans-serif;
    color: var(--text-dark);
  }
  .slide-header {
    position: absolute; left: 0; top: 0;
    width: 1200px; height: 99px;
    background: var(--header-teal);
  }
  .slide-title {
    position: absolute; left: 28px; top: 24px;
    font-family: "Ubuntu", Arial, sans-serif;
    font-weight: 400; font-size: 42px;
    color: var(--white);
  }
  .company-name {
    position: absolute; right: 16px; top: 46px;
    font-family: "Ubuntu", Arial, sans-serif;
    font-size: 25px; color: var(--white);
  }
  .section {
    position: absolute; left: 52px; top: 162px; width: 1100px;
  }
  .section-title {
    display: flex; align-items: center; gap: 16px;
    font-family: "Ubuntu", Arial, sans-serif;
    font-weight: 500; font-size: 24px;
    color: var(--heading-teal);
  }
  .section-marker {
    width: 14px; height: 14px; background: var(--heading-teal);
  }
  .section-text {
    margin: 8px 0 0 48px;
    font-size: 18px; line-height: 30px;
    color: var(--text-dark);
  }
  .chart { position: absolute; left: 0; top: 0; }
  .axis-label {
    font-family: "Roboto", Arial, sans-serif;
    font-size: 17px; fill: var(--text-dark);
  }
  .slide-footer {
    position: absolute; left: 0; bottom: 0;
    width: 1200px; height: 43px;
    background: var(--footer-teal);
  }
  .copyright {
    position: absolute; left: 12px; top: 10px;
    font-size: 19px; color: var(--white);
  }
</style>
</head>
<body>
<main class="slide">
  <header class="slide-header">
    <h1 class="slide-title">Graph data Heading</h1>
    <div class="company-name">Halden Ridge Capital, LLC</div>
  </header>

  <section class="section">
    <h2 class="section-title"><span class="section-marker"></span>Bullet Title Heading Here Bullet Title Heading Here</h2>
    <p class="section-text">Lorem ipsum dolor sit Lorem ipsum dolor sit&nbsp; Lorem ipsum dolor sit Lorem ipsum dolor sit&nbsp; Lorem ipsum dolor sit Lorem ipsum dolor sit&nbsp; Lorem ipsum dolor sit Lorem ipsum dolor sit&nbsp; Lorem ipsum dolor sit Lorem ipsum dolor sit&nbsp; Lorem ipsum dolor sit Lorem ipsum dolor sit&nbsp; Lorem ipsum dolor sit Lorem ipsum dolor sit&nbsp; Lorem ipsum dolor sit Lorem ipsum dolor sit</p>
  </section>

  <svg class="chart" width="1200" height="900" viewBox="0 0 1200 900" role="img" aria-label="Bar chart">
    <g text-anchor="end">
      <text class="axis-label" x="278" y="351">Lorem ipsum dolor sit</text>
      <text class="axis-label" x="278" y="399">Lorem ipsum dolor sit</text>
      <text class="axis-label" x="278" y="456">Lorem ipsum dolor sit</text>
      <text class="axis-label" x="278" y="512">Lorem ipsum dolor sit</text>
      <text class="axis-label" x="278" y="564">Lorem ipsum dolor sit</text>
      <text class="axis-label" x="278" y="624">Lorem ipsum dolor sit</text>
      <text class="axis-label" x="278" y="759">Lorem ipsum dolor sit</text>
    </g>
    <g>
      <rect x="295" y="620" width="48" height="138" fill="var(--bar-teal)"/>
      <rect x="354" y="509" width="62" height="249" fill="var(--bar-cyan)"/>
      <rect x="429" y="554" width="60" height="204" fill="var(--bar-teal)"/>
      <rect x="500" y="635" width="60" height="123" fill="var(--bar-sky)"/>
      <rect x="576" y="722" width="64" height="36" fill="var(--bar-sky)"/>
      <rect x="653" y="746" width="72" height="12" fill="var(--bar-grey)"/>
      <rect x="734" y="368" width="60" height="390" fill="var(--bar-teal)"/>
      <rect x="807" y="720" width="63" height="38" fill="var(--bar-deep)"/>
      <rect x="882" y="738" width="63" height="20" fill="var(--bar-teal)"/>
      <rect x="959" y="746" width="72" height="12" fill="var(--bar-grey)"/>
    </g>
    <line x1="294.5" y1="330" x2="294.5" y2="758" stroke="var(--axis)" stroke-width="1.5"/>
    <line x1="294" y1="758.5" x2="1032" y2="758.5" stroke="var(--axis)" stroke-width="1.5"/>
  </svg>

  <footer class="slide-footer">
    <p class="copyright">Copyright text here</p>
  </footer>
</main>
</body>
</html>
```